Design and Renovation Company Luxury Business Card

I want to create a luxury business card for a Design and Renovation Firm . We will use our current logo. The company name is 528BUILDA. We do not want anything standard. We need a very unique concept.
Please see uploaded inspiration. I really like the textured paper option. I would like the card to be thick with debossing, and/or embossing options. The logo has orange in it but I would like to see the card with and without the orange. I think the orange may make the company feel less high-end. The goal is to elevate the logo not match its vibe per se of the logo. We want something very unique, not standard at all!
I would like a space for :
Logo,
Name,
Position,
Email,
Office number,
Website Address,
Business Address,
Thank you!
Have fun!
Target Market(s)
Home owners Age 35 +
Industry/Entity Type
Design and Renovation
Contact Information for Business Card
Logo, Name, Position, Email, Office number, Website Address, Business Address,.
Colors
Designer to choose colors to be used in the design.
Requirements
Must have
- A luxury designer feel. Must be black or dark grey but open to other luxury ideas.
Nice to have
- Gold, silver, black embossing or debossing. Textured paper design.
Should not have
- A cheap look and feel.

```html
<!DOCTYPE html>
<html lang="en">
<head>
<meta charset="utf-8">
<title>528BUILDA — Business Card</title>
<link rel="stylesheet" href="https://fonts.googleapis.com/css2?family=Arimo:wght@400;700&display=swap">
<style>
  :root {
    --backdrop: #9a9a9a;
    --card-front: #3b3b3b;
    --card-front-deep: #333333;
    --card-back: #2a2a2a;
    --ink-white: #f4f4f4;
    --ink-soft: #e2e2e2;
    --accent: #f29a2e;
    --edge: #f7f7f7;
  }
  * { box-sizing: border-box; margin: 0; padding: 0; }
  html, body { width: 1200px; height: 1050px; overflow: hidden; }
  body {
    background: var(--backdrop);
    font-family: "Arimo", Arial, sans-serif;
    position: relative;
  }
  .card {
    position: absolute;
    border-radius: 26px;
    border: 2px solid var(--edge);
    box-shadow: 0 14px 30px rgba(0,0,0,0.25);
  }

  /* Front: portrait contact side */
  .card-front {
    left: 90px; top: 192px;
    width: 380px; height: 665px;
    background: radial-gradient(circle at 30% 20%, var(--card-front), var(--card-front-deep));
    display: flex; flex-direction: column; align-items: center;
    padding-top: 110px;
    color: var(--ink-white);
    text-align: center;
  }
  .brand-mark {
    display: flex; align-items: center; gap: 14px;
    margin-bottom: 70px;
  }
  .brand-mark .square {
    width: 34px; height: 34px; background: var(--ink-white);
  }
  .brand-mark .brand-name {
    font-weight: 700; font-size: 34px; letter-spacing: 1px;
    color: var(--ink-white);
  }
  .person-name {
    color: var(--accent); font-weight: 700; font-size: 26px; line-height: 1.1;
  }
  .person-role {
    font-size: 20px; color: var(--ink-soft); margin-top: 2px;
  }
  .divider {
    width: 38px; height: 2px; background: var(--ink-soft);
    margin: 40px 0;
  }
  .address {
    font-size: 19px; line-height: 1.35; color: var(--ink-soft);
  }
  .contact-list { list-style: none; font-size: 19px; line-height: 1.4; color: var(--ink-soft); text-align: left; }
  .contact-list .label { color: var(--accent); font-weight: 700; margin-right: 6px; }

  /* Back: landscape brand side */
  .card-back {
    left: 520px; top: 342px;
    width: 640px; height: 366px;
    background: var(--card-back);
    display: flex; align-items: center; justify-content: center;
  }
  .brand-lockup { display: flex; flex-direction: column; align-items: flex-start; }
  .brand-lockup .row { display: flex; align-items: center; gap: 18px; }
  .brand-lockup .square { width: 48px; height: 48px; background: var(--ink-white); }
  .brand-lockup .brand-name {
    font-weight: 700; font-size: 66px; letter-spacing: 2px; color: var(--ink-white); line-height: 1;
  }
  .tagline {
    margin-top: 10px; margin-left: 66px;
    font-weight: 700; font-size: 15px; letter-spacing: 6px; color: var(--ink-white);
  }
</style>
</head>
<body>
  <section class="card card-front" aria-label="Contact side">
    <div class="brand-mark">
      <span class="square"></span>
      <span class="brand-name">528BUILDA</span>
    </div>
    <p class="person-name">Daniel Porter</p>
    <p class="person-role">President</p>
    <span class="divider"></span>
    <p class="address">4127 Harrow Lane<br>Glen Cove, NY 11542</p>
    <span class="divider"></span>
    <ul class="contact-list">
      <li><span class="label">P :</span>(555) 2190-4471</li>
      <li><span class="label">E :</span>name@528BUILDA.com</li>
      <li><span class="label">W :</span>www.528BUILDA.com</li>
    </ul>
  </section>

  <section class="card card-back" aria-label="Brand side">
    <div class="brand-lockup">
      <div class="row">
        <span class="square"></span>
        <span class="brand-name">528BUILDA</span>
      </div>
      <p class="tagline">Design and Renovation Firm</p>
    </div>
  </section>
</body>
</html>
```